Brightway Coordination Group Business card

We wish to have a professional Business card to present to large Corporate CEO's ASAP.

Our web site helps explain our business www.brightwaycg.org

Brightway Coordination Group was established after we discovered how difficult it is to organise outsourced services while heading up a business or company.

We act as a facilitator for businesses who don't have the desire, expertise or recourses to manage their own systems and meet all their requirements.

We provide an all in one facility management solution for all types of businesses. We manage schedules, contractors and costs on behalf of businesses and their needs and wants.

Having an extensive network ensures we are able to connect businesses with the right service providers.

Target Market(s)

Company CEO

Industry/Entity Type

Business

Font styles to use
Sans Serif

Colors
33a6d7
f9fdfe
0355a3

Requirements
Must have
• professional design
Nice to have
• colours to match logo

```html
<!DOCTYPE html>
<html lang="en">
<head>
<meta charset="utf-8">
<title>Brightway Coordination Group – Business Card</title>
<link rel="stylesheet" href="https://fonts.googleapis.com/css2?family=Lato:wght@300;400;700&display=swap">
<style>
  :root {
    --brand-blue: #0355a3;
    --brand-sky: #33a6d7;
    --brand-white: #f9fdfe;
    --ink: #1a1a1a;
    --back-ink: #0b2c55;
    --tab-black: #1c1c1c;
    --panel-light: #f4f4f4;
    --stage: #2b2b2b;
  }
  html, body {
    margin: 0;
    padding: 0;
    width: 1200px;
    height: 997px;
    overflow: hidden;
    background: var(--stage);
    font-family: "Lato", sans-serif;
  }
  .stage {
    position: relative;
    width: 1200px;
    height: 997px;
  }
  .card {
    position: absolute;
    width: 540px;
    height: 310px;
    border-radius: 18px;
    overflow: hidden;
    box-shadow: 0 18px 40px rgba(0,0,0,0.55);
  }
  /* Back of card */
  .card-back {
    left: 70px;
    top: 150px;
    background: linear-gradient(160deg, #1266bb 0%, var(--brand-blue) 60%, #02468a 100%);
  }
  .back-brand {
    position: absolute;
    right: 36px;
    top: 118px;
    text-align: right;
  }
  .back-tagline {
    font-size: 11px;
    letter-spacing: 1px;
    color: var(--back-ink);
    font-weight: 400;
  }
  .back-name {
    margin-top: 4px;
    font-size: 17px;
    font-weight: 700;
    letter-spacing: 1px;
    color: var(--back-ink);
  }
  /* Front of card */
  .card-front {
    left: 590px;
    top: 470px;
    background: var(--panel-light);
  }
  .card-front svg.bands {
    position: absolute;
    inset: 0;
  }
  .holder-name {
    position: absolute;
    left: 28px;
    top: 14px;
    font-size: 22px;
    letter-spacing: 1px;
    color: var(--brand-white);
    font-weight: 300;
  }
  .holder-name b { font-weight: 700; }
  .holder-role {
    position: absolute;
    right: 26px;
    top: 12px;
    font-size: 14px;
    letter-spacing: 1px;
    color: #dcdcdc;
  }
  .front-brand {
    position: absolute;
    left: 60px;
    top: 118px;
    display: flex;
    align-items: center;
    gap: 10px;
  }
  .brand-dot {
    width: 30px;
    height: 30px;
    border-radius: 50%;
    background: var(--brand-sky);
  }
  .brand-name {
    font-size: 20px;
    font-weight: 700;
    letter-spacing: 0.5px;
    color: var(--ink);
  }
  .contact {
    position: absolute;
    display: flex;
    align-items: center;
    gap: 8px;
    font-size: 13px;
    color: var(--ink);
    font-weight: 700;
  }
  .contact-email { right: 30px; top: 190px; }
  .contact-phone { left: 26px; top: 208px; }
  .contact-icon {
    width: 26px;
    height: 26px;
    border-radius: 50%;
    background: var(--brand-blue);
    display: flex;
    align-items: center;
    justify-content: center;
  }
  .website {
    position: absolute;
    left: 0;
    right: 0;
    bottom: 20px;
    text-align: center;
    font-size: 15px;
    letter-spacing: 3px;
    font-weight: 700;
    color: var(--brand-white);
  }
</style>
</head>
<body>
<main class="stage">

  <section class="card card-back" aria-label="Card back">
    <div class="back-brand">
      <div class="back-tagline">FACILITY COORDINATION</div>
      <div class="back-name">BRIGHTWAY COORDINATION GROUP</div>
    </div>
  </section>

  <section class="card card-front" aria-label="Card front">
    <svg class="bands" width="540" height="310" viewBox="0 0 540 310" aria-hidden="true">
      <defs>
        <linearGradient id="panelShade" x1="0" y1="0" x2="0" y2="1">
          <stop offset="0" stop-color="#ffffff"/>
          <stop offset="1" stop-color="#dedede"/>
        </linearGradient>
      </defs>
      <rect x="0" y="0" width="540" height="310" fill="url(#panelShade)"/>
      <rect x="360" y="0" width="180" height="52" fill="var(--tab-black)"/>
      <path d="M0 0 H420 Q395 0 385 30 Q378 52 350 56 H0 Z" fill="var(--brand-blue)"/>
      <rect x="0" y="56" width="540" height="4" fill="var(--tab-black)"/>
      <rect x="0" y="240" width="540" height="6" fill="var(--tab-black)"/>
      <rect x="0" y="246" width="540" height="64" fill="var(--brand-blue)"/>
    </svg>

    <div class="holder-name">DANIEL <b>HARWOOD</b></div>
    <div class="holder-role">OWNER</div>

    <div class="front-brand">
      <span class="brand-dot"></span>
      <span class="brand-name">BRIGHTWAY COORDINATION GROUP</span>
    </div>

    <div class="contact contact-email">
      <span class="contact-icon">
        <svg width="14" height="10" viewBox="0 0 14 10" aria-hidden="true">
          <rect x="0.5" y="0.5" width="13" height="9" fill="none" stroke="#fff"/>
          <path d="M0.5 0.5 L7 5.5 L13.5 0.5" fill="none" stroke="#fff"/>
        </svg>
      </span>
      daniel@brightwaycg.org
    </div>

    <div class="contact contact-phone">
      <span class="contact-icon">
        <svg width="14" height="14" viewBox="0 0 24 24" aria-hidden="true">
          <path fill="#fff" d="M6.6 10.8a15.1 15.1 0 0 0 6.6 6.6l2.2-2.2a1 1 0 0 1 1-.25 11.4 11.4 0 0 0 3.6.57 1 1 0 0 1 1 1V20a1 1 0 0 1-1 1A17 17 0 0 1 3 4a1 1 0 0 1 1-1h3.5a1 1 0 0 1 1 1c0 1.250.2 2.45.57 3.6a1 1 0 0 1-.25 1z"/>
        </svg>
      </span>
      0400 128 976
    </div>

    <div class="website">www.brightwaycg.org</div>
  </section>

</main>
</body>
</html>
```